Real estate broker business card

Want a modern celan but effective business card for my residential and commercial real estate business. I want the back of the card to advertise my services and to capture business. I have attached the back of my current business card fore ideas
Updates

Logos, photo and text updates added! Added Saturday, September 3, 2016

Project Deadline Extended Reason: LOGOS, PHOTOS AND TEST JUST UPLOADED! I'M READY TO PICK A DESIGN! THANK YOU! Added Saturday, September 3, 2016

Target Market(s)

home buyers and seller. commercial buyers and sellers

Industry/Entity Type

Real Estate

Contact Information for Business Card

must have my contact information and my photo

Requirements
Must have
• Carla Ventrino
• Owner & Qualifying Broker
• Ventrino Real Estate Services
• 505.718.2094
• carla@ventrinohomes.example
• www.ventrinohomes.example
Nice to have
• metallic
• Business capture text: " Don't buy or lease property without someone looking out for your best interests. I will represent you on your home or investment purchase for FREE!"
• "Home owners, call today to receive a FREE market analysis for your homes value!

```html
<!DOCTYPE html>
<html lang="en">
<head>
<meta charset="utf-8">
<title>Ventrino Real Estate Services – Business Card</title>
<link rel="stylesheet" href="https://fonts.googleapis.com/css2?family=Open+Sans:wght@400;600&display=swap">
<style>
  :root {
    --stage: #000000;
    --card: #343538;
    --card-edge: #3a3b3f;
    --teal: #2f8d9c;
    --text-light: #e9eaec;
    --photo-dark: #2a1c17;
    --photo-mid: #6b4a3c;
    --photo-light: #d9cfc9;
  }
  * { margin: 0; padding: 0; box-sizing: border-box; }
  html, body {
    width: 1200px; height: 900px; overflow: hidden;
    background: var(--stage);
    font-family: "Open Sans", Arial, sans-serif;
  }
  .canvas { position: relative; width: 1200px; height: 900px; }
  .card {
    position: absolute; top: 271px;
    width: 457px; height: 281px;
    border-radius: 14px;
    background: radial-gradient(ellipse at 50% 40%, var(--card-edge), var(--card) 75%);
    overflow: hidden;
  }
  .card-front { left: 137px; }
  .card-back { left: 626px; }

  .portrait {
    position: absolute; left: 0; top: 0;
    width: 186px; height: 281px;
    background: linear-gradient(180deg, var(--photo-dark) 0%, var(--photo-mid) 45%, var(--photo-light) 80%, #eee8e4 100%);
    border-radius: 0 60px 40px 0 / 0 120px 90px 0;
  }

  .contact { position: absolute; left: 256px; top: 86px; color: var(--text-light); }
  .contact-name { color: var(--teal); font-weight: 600; font-size: 14.5px; line-height: 18px; }
  .contact-title { font-size: 12px; line-height: 17px; }
  .contact-list { list-style: none; margin-top: 23px; }
  .contact-list li {
    display: flex; align-items: center;
    font-size: 12px; line-height: 16.5px;
    letter-spacing: -0.1px;
    white-space: nowrap;
  }
  .contact-list svg { width: 9px; height: 9px; margin-right: 9px; fill: var(--teal); flex: none; }

  .brand {
    position: absolute; left: 0; right: 0; top: 40px;
    display: flex; flex-direction: column; align-items: center;
    color: var(--teal); font-weight: 400; text-transform: uppercase;
  }
  .brand-mark {
    width: 74px; height: 74px; border-radius: 50%;
    background: var(--teal);
  }
  .brand-name {
    margin-top: 38px;
    font-size: 46px; line-height: 46px;
    letter-spacing: 3px;
  }
  .brand-tagline {
    margin-top: 6px;
    font-size: 15px; line-height: 18px;
    letter-spacing: 2.6px;
  }
</style>
</head>
<body>
<div class="canvas">
  <section class="card card-front">
    <div class="portrait" role="img" aria-label="Portrait photo of Carla Ventrino"></div>
    <div class="contact">
      <p class="contact-name">Carla Ventrino</p>
      <p class="contact-title">Owner &amp; Qualifying Broker</p>
      <ul class="contact-list">
        <li>
          <svg viewBox="0 0 10 10" aria-hidden="true"><path d="M2 0.5 L3.6 2.6 L2.7 3.6 Q3.8 5.9 6.4 7.3 L7.4 6.4 L9.5 8 L8.3 9.5 Q3.5 8.6 0.5 1.7 Z"/></svg>
          505.718.2094
        </li>
        <li>
          <svg viewBox="0 0 10 10" aria-hidden="true"><path d="M0.5 2 H9.5 V8.5 H0.5 Z M1 2.4 L5 5.6 L9 2.4" stroke="#343538" stroke-width="0.8"/></svg>
          carla@ventrinohomes.example
        </li>
        <li>
          <svg viewBox="0 0 10 10" aria-hidden="true"><circle cx="5" cy="5" r="4.5"/><path d="M0.5 5 H9.5 M5 0.5 V9.5" stroke="#343538" stroke-width="0.7"/></svg>
          www.ventrinohomes.example
        </li>
      </ul>
    </div>
  </section>

  <section class="card card-back">
    <div class="brand">
      <span class="brand-mark" aria-hidden="true"></span>
      <p class="brand-name">Ventrino</p>
      <p class="brand-tagline">Real Estate Services</p>
    </div>
  </section>
</div>
</body>
</html>
```